We (R. T. Galvin & Partners, Inc.) are an executive Search firm based in Los Angeles that is exclusively focused in the Med Tech and Health Tech arenas.   I need a logo to communicate that we are a high end search firm, but also that we are focused in the medicine and science arenas called health tech and med tech.  Many of our clients have robotics and artificial intelligence type products, so it is very technology forward.  I tend to gravitate towards clean, sharp aesthetic as opposed to something that is really over the top.
Attached are files with my logo in two different layouts.  In addition to the letterhead and envelope, I also will need an electronic letterhead in Microsoft Word.  I tend to
I look forward to seeing the designs and just let me know if you have any questions.
Dale

```html
<!DOCTYPE html>
<html lang="en">
<head>
<meta charset="UTF-8">
<title>R. T. Galvin &amp; Partners, Inc. — Business Card</title>
<link href="https://fonts.googleapis.com/css2?family=Roboto:wght@400;500&display=swap" rel="stylesheet">
<style>
  :root {
    --bg-outer: #4a4a4a;
    --bg-inner: #2a2a2a;
    --card: #1d1d1f;
    --accent: #3f9be0;
    --ink: #f2f2f2;
    --ink-soft: #d6d6d6;
  }
  * { margin: 0; padding: 0; box-sizing: border-box; }
  html, body {
    width: 1200px; height: 900px; overflow: hidden;
  }
  body {
    background: radial-gradient(ellipse at 50% 40%, var(--bg-outer), var(--bg-inner));
    font-family: "Roboto", Arial, sans-serif;
    color: var(--ink);
    position: relative;
  }
  .card {
    position: absolute;
    width: 560px; height: 320px;
    background: var(--card);
    border-radius: 24px;
    box-shadow: 0 18px 40px rgba(0,0,0,.5);
  }
  .card--back { left: 320px; top: 70px; }
  .card--front { left: 320px; top: 480px; }

  .brand {
    display: flex; align-items: center; gap: 14px;
  }
  .brand__dot {
    width: 34px; height: 34px; border-radius: 50%;
    background: var(--accent); flex: none;
  }
  .brand__name {
    font-weight: 500; color: var(--ink);
    text-transform: uppercase; letter-spacing: 1.5px; line-height: 1.15;
  }
  .card--back .brand {
    position: absolute; left: 50%; top: 50%;
    transform: translate(-50%, -50%);
  }
  .card--back .brand__name { font-size: 24px; }
  .card--back .brand__dot { width: 44px; height: 44px; }

  .card--front .brand {
    position: absolute; left: 34px; top: 62px; width: 200px;
    flex-direction: column; align-items: flex-start; gap: 12px;
  }
  .card--front .brand__name { font-size: 15px; }

  .divider {
    position: absolute; left: 250px; top: 40px; bottom: 40px;
    width: 1px; background: var(--accent); opacity: .7;
  }
  .contact {
    position: absolute; left: 272px; top: 44px; right: 24px;
  }
  .contact__name {
    color: var(--accent); font-weight: 500; font-size: 27px;
    text-transform: uppercase; letter-spacing: 1px;
  }
  .contact__role { font-size: 14px; color: var(--ink-soft); margin: 4px 0 14px; }
  .contact__address { font-size: 14px; line-height: 1.45; color: var(--ink); margin-bottom: 10px; }
  .contact__list { list-style: none; font-size: 14px; line-height: 1.55; }
  .contact__list li { display: flex; align-items: center; gap: 8px; }
  .contact__list svg { width: 12px; height: 12px; fill: var(--accent); flex: none; }
</style>
</head>
<body>
  <section class="card card--back">
    <div class="brand">
      <span class="brand__dot"></span>
      <span class="brand__name">R. T. Galvin<br>&amp; Partners, Inc.</span>
    </div>
  </section>

  <section class="card card--front">
    <div class="brand">
      <span class="brand__dot"></span>
      <span class="brand__name">R. T. Galvin<br>&amp; Partners, Inc.</span>
    </div>
    <div class="divider"></div>
    <div class="contact">
      <h1 class="contact__name">Dale Whitford</h1>
      <p class="contact__role">Director</p>
      <p class="contact__address">418 Cedarline Avenue<br>Los Angeles, CA 90012</p>
      <ul class="contact__list">
        <li><svg viewBox="0 0 24 24"><path d="M6.6 10.8a15.1 15.1 0 0 0 6.6 6.6l2.2-2.2c.3-.3.7-.4 1-.2 1.1.4 2.3.6 3.6.6.6 0 1 .4 1 1V20c0 .6-.4 1-1 1C10.6 21 3 13.4 3 4c0-.6.4-1 1-1h3.5c.6 0 1 .4 1 1 0 1.3.2 2.5.6 3.6.1.3 0 .7-.2 1z"/></svg>+1 (213) 555-0148</li>
        <li><svg viewBox="0 0 24 24"><path d="M7 1h10a2 2 0 0 1 2 2v18a2 2 0 0 1-2 2H7a2 2 0 0 1-2-2V3a2 2 0 0 1 2-2zm0 3v14h10V4zm5 15.5a1 1 0 1 0 0 2 1 1 0 0 0 0-2z"/></svg>+1 (213) 555-0192</li>
        <li><svg viewBox="0 0 24 24"><path d="M2 5h20v14H2zm2 2v.5l8 5 8-5V7zm0 2.8V17h16V9.8l-8 5z"/></svg>dale@rtgalvinpartners.com</li>
        <li><svg viewBox="0 0 24 24"><path d="M12 2a10 10 0 1 0 0 20 10 10 0 0 0 0-20zm6.9 9h-3a15 15 0 0 0-1.3-5.6A8 8 0 0 1 18.9 11zM12 4c1 1.3 1.8 3.9 1.9 7h-3.8C10.2 7.9 11 5.3 12 4zM9.4 5.4A15 15 0 0 0 8.1 11h-3a8 8 0 0 1 4.3-5.6zM5.1 13h3a15 15 0 0 0 1.3 5.6A8 8 0 0 1 5.1 13zM12 20c-1-1.3-1.8-3.9-1.9-7h3.8c-.1 3.1-.9 5.7-1.9 7zm2.6-1.4a15 15 0 0 0 1.3-5.6h3a8 8 0 0 1-4.3 5.6z"/></svg>www.rtgalvinpartners.com</li>
      </ul>
    </div>
  </section>
</body>
</html>
```